Blind Rivet Product catalogue

Need a design in wordpress with a productcatalogue where i present all products. This is a B2B business. The products is Blindrivets and Blindrivet nuts and accessories to this. I only want the basic information and also technical specification.

This is a subcompany to my existing company k7.m3.se but specializing in a subcategory

Businesses using blind rivet technology.

Industrial

Sans Serif

Must have
• Three different categories for the products; Blind Rivets - Blind Rivet Nut - Riveting Tools
Nice to have
• Possible to ad login for more information of the different sizes

```html
<!DOCTYPE html>
<html lang="en">
<head>
<meta charset="utf-8">
<title>Blind Rivet – Product Catalogue</title>
<link href="https://fonts.googleapis.com/css2?family=Lato:wght@400;700;900&display=swap" rel="stylesheet">
<style>
:root{
  --ink:#222;
  --text:#444;
  --muted:#666;
  --red:#d9151b;
  --green:#5bbd3c;
  --green-light:#8cc63f;
  --black:#000;
  --band:#f1f1f1;
  --line:#d0d0d0;
}
*{box-sizing:border-box;margin:0;padding:0}
html,body{width:1200px;height:3340px;overflow:hidden}
body{font-family:'Lato',sans-serif;color:var(--text);background:#fff;font-size:15px}
.wrap{width:1050px;margin:0 auto;position:relative}

.topbar{height:52px;display:flex;align-items:center}
.topbar .wrap{display:flex;align-items:center;justify-content:space-between}
.social{display:flex;gap:14px}
.dot{width:18px;height:18px;border-radius:50%;background:#333;display:inline-block}
.top-right{display:flex;align-items:center;gap:40px}
.search{width:300px;height:28px;border:1px solid #999;display:flex;align-items:center;justify-content:space-between;padding:0 10px;font-size:13px;color:#333}
.login{font-size:14px;color:#222;display:flex;align-items:center;gap:10px}

.header{height:123px;background:var(--black)}
.header .wrap{display:flex;align-items:center;height:100%}
.brand{width:145px;display:flex;align-items:center;gap:8px;color:#ccc;font-weight:700;font-size:24px;padding-left:33px}
.brand-mark{width:14px;height:14px;background:var(--red)}
.perk{display:flex;align-items:center;gap:18px;margin-left:62px}
.perk:first-of-type{margin-left:0}
.perk h4{color:var(--green-light);font-weight:400;font-size:15.5px;letter-spacing:.3px}
.perk p{color:#fff;font-size:14.5px;margin-top:5px}

.nav{height:58px;border-bottom:1px solid #eee}
.nav .wrap{display:flex;align-items:center;height:100%;padding-left:-3px}
.nav a{font-size:14px;color:#111;text-decoration:none;padding:0 21px;height:58px;display:flex;align-items:center}
.nav a.active{color:var(--red);border-bottom:3px solid var(--red)}
.cart{position:absolute;right:0;top:18px}
.cart span{position:absolute;left:18px;top:-8px;width:20px;height:20px;border-radius:50%;background:var(--green);color:#fff;font-size:12px;font-weight:700;display:flex;align-items:center;justify-content:center}

.hero{height:610px;background:radial-gradient(ellipse at 70% 45%,#fff 0%,#f2f2f2 55%,#e6e6e6 100%);position:relative}
.hero-copy{position:absolute;left:91px;top:202px}
.hero-copy h3{font-size:35px;font-weight:900;color:var(--ink)}
.hero-copy h1{font-size:60px;font-weight:900;color:var(--ink);line-height:1}
.hero-copy p{font-size:22px;font-weight:700;color:#333;margin-top:12px}
.btn{display:inline-block;background:var(--green);color:#fff;text-decoration:none;font-size:18px}
.hero-copy .btn{margin-top:24px;padding:14px 32px}
.hero-art{position:absolute;left:540px;top:70px;width:580px;height:440px;border-radius:50%;background:radial-gradient(circle,#b8bcc0 0%,#d8dadc 50%,rgba(240,240,240,0) 72%)}
.arrow{position:absolute;top:286px}

.section-title{text-align:center;font-size:34px;font-weight:700;color:var(--ink)}
.categories{padding-top:52px}
.cat-grid{display:flex;justify-content:space-between;margin-top:36px}
.cat{width:330px;text-align:center}
.cat-img{height:273px;border:2px solid var(--line);background:radial-gradient(circle at 50% 50%,#fff,#e9e9e9)}
.cat h3{color:var(--red);font-size:24px;font-weight:900;margin-top:18px}
.cat p{font-size:15px;color:#555;margin-top:14px}
.divider{border:0;border-top:1px solid var(--line);margin-top:72px}

.featured{padding-top:50px;height:582px}
.prod-grid{display:flex;justify-content:space-between;margin-top:30px}
.prod{width:241px;height:390px;text-align:center;padding-top:25px;border:2px solid transparent}
.prod.hover{border-color:var(--line)}
.prod-img{width:190px;height:150px;margin:0 auto;background:radial-gradient(circle,#c4c6c8,#fff 70%)}
.prod h4{font-size:18px;color:#333;margin-top:38px;font-weight:700}
.prod .sub{font-size:15px;color:#555;margin-top:10px}
.prod .old{font-size:15px;color:#777;text-decoration:line-through;margin-top:10px}
.prod .price{font-size:18px;color:var(--red);font-weight:700;margin-top:6px}
.prod .btn{margin-top:20px;padding:8px 26px;font-size:17px}

.about{height:335px;background:var(--band);text-align:center;padding-top:50px}
.about p{width:1040px;margin:26px auto 0;font-size:15px;line-height:1.6;color:#444}
.about .btn{margin-top:32px;padding:16px 32px;font-size:17px}

.banners{height:393px;padding-top:55px}
.banners .wrap{display:flex;justify-content:space-between}
.banner{width:512px;height:274px;display:flex;align-items:center;justify-content:center;color:#fff;font-size:40px;font-weight:700}
.b1{background:linear-gradient(135deg,#4a5560,#6b7680 50%,#3c454d)}
.b2{background:linear-gradient(135deg,#2a2f35,#4a4f52 50%,#7a6a5e)}

.mailing{height:267px;background:var(--band);text-align:center;padding-top:58px}
.mailing p{font-size:15px;color:#333;margin-top:22px}
.subscribe{width:500px;height:41px;margin:34px auto 0;border:2px solid #999;display:flex;background:#fff}
.subscribe span{flex:1;text-align:left;padding:11px 14px;font-size:15px;color:#333}
.subscribe b{width:46px;background:var(--green);display:flex;align-items:center;justify-content:center}

.footer{height:300px;padding-top:50px}
.footer .wrap{display:flex}
.footer h5{font-size:17px;color:#222;font-weight:700;margin-bottom:20px}
.col a{display:block;font-size:15px;color:#444;text-decoration:none;margin-bottom:18px}
.col-site{width:337px}
.col-site .links{display:grid;grid-template-columns:133px 133px}
.col-help{width:240px}
.col-acct{width:233px}
.col-acct a{margin-bottom:15px}
.col-social .social{gap:26px}
.col-social .dot{width:24px;height:24px}
.pay{display:grid;grid-template-columns:repeat(3,42px);gap:15px 17px;margin-top:6px}
.pay i{height:25px;border-radius:3px;background:#c9d2e0;display:block}
.copyright{border-top:1px solid #ddd;text-align:center;font-size:13px;color:#333;padding-top:28px;position:relative;height:70px}
.copyright .ver{position:absolute;right:12px;top:28px}
</style>
</head>
<body>

<div class="topbar">
  <div class="wrap">
    <div class="social"><i class="dot"></i><i class="dot"></i><i class="dot"></i><i class="dot"></i></div>
    <div class="top-right">
      <div class="search">Search..
        <svg width="14" height="14" viewBox="0 0 14 14"><circle cx="6" cy="6" r="4.5" fill="none" stroke="#d9151b" stroke-width="2"/><line x1="9.5" y1="9.5" x2="13" y2="13" stroke="#d9151b" stroke-width="2"/></svg>
      </div>
      <div class="login"><svg width="14" height="16" viewBox="0 0 14 16"><circle cx="7" cy="4.5" r="4" fill="#222"/><path d="M0 16c0-5 3-7 7-7s7 2 7 7z" fill="#222"/></svg>LOG IN</div>
    </div>
  </div>
</div>

<header class="header">
  <div class="wrap">
    <div class="brand"><span class="brand-mark"></span>K7M3</div>
    <div class="perk" style="margin-left:100px">
      <svg width="30" height="24" viewBox="0 0 30 24"><rect x="0" y="3" width="18" height="14" fill="#777"/><path d="M18 7h7l5 6v4H18z" fill="#777"/><circle cx="6" cy="20" r="3" fill="#777"/><circle cx="24" cy="20" r="3" fill="#777"/></svg>
      <div><h4>FREE DELIVERY WORLDWIDE</h4><p>Click here for more info</p></div>
    </div>
    <div class="perk">
      <svg width="26" height="26" viewBox="0 0 26 26"><path d="M2 2h11l11 11-11 11L2 13z" fill="#777"/><circle cx="7" cy="7" r="2" fill="#000"/></svg>
      <div><h4>FINAL CLEARANCE SALE</h4><p>Up to 70% off</p></div>
    </div>
    <div class="perk" style="margin-left:44px">
      <svg width="30" height="24" viewBox="0 0 30 24"><path d="M11 2L1 11l10 9v-6c8 0 13 2 17 8-1-9-6-15-17-15z" fill="#777"/></svg>
      <div><h4>EASY RETURN</h4><p>Click here for more info</p></div>
    </div>
  </div>
</header>

<nav class="nav">
  <div class="wrap">
    <a class="active" href="#">HOME</a><a href="#">ABOUT US</a><a href="#">PRODUCTS</a><a href="#">SHOP</a><a href="#">BLOG</a><a href="#">REVIEWS</a><a href="#">CONTACT US</a>
    <div class="cart"><svg width="20" height="18" viewBox="0 0 20 18"><path d="M0 1h4l3 10h10l2-7H6" fill="none" stroke="#111" stroke-width="2.4"/><circle cx="8" cy="15" r="2" fill="#111"/><circle cx="16" cy="15" r="2" fill="#111"/></svg><span>0</span></div>
  </div>
</nav>

<section class="hero">
  <svg class="arrow" style="left:58px" width="20" height="36" viewBox="0 0 20 36"><path d="M18 2L2 18l16 16" fill="none" stroke="#333" stroke-width="2"/></svg>
  <div class="hero-copy">
    <h3>WELCOME TO</h3>
    <h1>BLIND RIVET</h1>
    <p>Curabitur rhoncus suscipit mi in vulputate..</p>
    <a class="btn" href="#">Shop Now</a>
  </div>
  <div class="hero-art" role="img" aria-label="Pile of silver blind rivets"></div>
  <svg class="arrow" style="right:58px" width="20" height="36" viewBox="0 0 20 36"><path d="M2 2l16 16L2 34" fill="none" stroke="#333" stroke-width="2"/></svg>
</section>

<section class="categories">
  <div class="wrap">
    <h2 class="section-title">Categories</h2>
    <div class="cat-grid">
      <div class="cat"><div class="cat-img" role="img" aria-label="Single blind rivet"></div><h3>Blind Rivets</h3><p>Aliquam molestie, mi et imperdiet euismod</p></div>
      <div class="cat"><div class="cat-img" role="img" aria-label="Knurled blind rivet nut"></div><h3>Blind Rivet Nut</h3><p>Aliquam molestie, mi et imperdiet euismod</p></div>
      <div class="cat"><div class="cat-img" role="img" aria-label="Cordless riveting tool"></div><h3>Riveting Tools</h3><p>Aliquam molestie, mi et imperdiet euismod</p></div>
    </div>
    <hr class="divider">
  </div>
</section>

<section class="featured">
  <div class="wrap">
    <h2 class="section-title">Featured Products</h2>
    <div class="prod-grid">
      <div class="prod hover"><div class="prod-img" role="img" aria-label="Threaded rivet nuts"></div><h4>PRODUCT NAME</h4><p class="sub">Aliquam molestie</p><p class="old">$79.00</p><p class="price">$55.00</p><a class="btn" href="#">Add to Cart</a></div>
      <div class="prod"><div class="prod-img" role="img" aria-label="Black blind rivet"></div><h4>PRODUCT NAME</h4><p class="sub">Aliquam molestie</p><p class="old">$79.00</p><p class="price">$55.00</p></div>
      <div class="prod"><div class="prod-img" role="img" aria-label="Knurled blind rivet nut"></div><h4>PRODUCT NAME</h4><p class="sub">Aliquam molestie</p><p class="old">$79.00</p><p class="price">$55.00</p></div>
      <div class="prod"><div class="prod-img" role="img" aria-label="Cordless riveting tool"></div><h4>PRODUCT NAME</h4><p class="sub">Aliquam molestie</p><p class="old">$79.00</p><p class="price">$55.00</p></div>
    </div>
  </div>
</section>

<section class="about">
  <h2 class="section-title">About Blind Rivet</h2>
  <p>Aliquam molestie, mi et imperdiet euismod, dui purus auctor tellus,  et interdum lacus lectus et ante. Sed accumsan sollicitudin sapien, sit amet adipiscing turpis gravida ac. In congue, neque ac lobortis volutpat, libero mauris varius mi, vitae suscipit ipsum ligula vitae risus. Duis aliquam nibh a dui iaculis viverra id a velit. Vivamus egestas risus in magna varius commodo.</p>
  <a class="btn" href="#">Read More</a>
</section>

<section class="banners">
  <div class="wrap">
    <div class="banner b1" role="img" aria-label="Heap of bolts and nuts">Infastning</div>
    <div class="banner b2" role="img" aria-label="Hands working on a marine engine">Marin</div>
  </div>
</section>

<section class="mailing">
  <h2 class="section-title">Join our Mailing List</h2>
  <p>Nunc maximus, nisl sit amet sollicitudin euismod, orci pharetra nisi, non ultrices eros metus ac dui</p>
  <div class="subscribe"><span>Enter Email Address</span><b><svg width="12" height="16" viewBox="0 0 12 16"><path d="M2 2l6 6-6 6" fill="none" stroke="#fff" stroke-width="3"/></svg></b></div>
</section>

<footer class="footer">
  <div class="wrap">
    <div class="col col-site"><h5>SITE MAP</h5>
      <div class="links"><a href="#">Home</a><a href="#">Blog</a><a href="#">About Us</a><a href="#">Reviews</a><a href="#">Products</a><a href="#">Contact Us</a><a href="#">Shop</a></div>
    </div>
    <div class="col col-help"><h5>HELP</h5><a href="#">Delivery</a><a href="#">Returns</a><a href="#">Contact</a><a href="#">FAQs</a><a href="#">Size Guide</a></div>
    <div class="col col-acct"><h5>MY ACCOUNT</h5><a href="#">Log In</a><a href="#">Register</a><a href="#">Help</a><a href="#">Wishlist</a></div>
    <div class="col col-social"><h5>SOCIAL NETWORKS</h5>
      <div class="social"><i class="dot"></i><i class="dot"></i><i class="dot"></i><i class="dot"></i></div>
      <h5 style="margin-top:38px">PAYMENT</h5>
      <div class="pay"><i></i><i></i><i></i><i></i><i></i><i></i></div>
    </div>
  </div>
</footer>
<div class="copyright">Copyright © 2020. Company Name. All Right Reserved<span class="ver">X10</span></div>

</body>
</html>
```